Business Card Design

educational services
broker of essential services
So I love my The Velvet Kettle cards. I love the background.
I like the background on the copper valley card
I like a little part of each Meridel card
I want my card to stand out and be professional
I would also like somewhat of a brand
I do not want it to be specific to anything but the world and galaxy
I would like to be able to be used for everything, all encompassing
In spanish Cielo abierto, not sureother languages but i will do programs for other countries like China, Japan and Korea
Reason: It has been the first week of school and I have not been able to get the feedback I need.
Please change colors to Blue and GOld
Please add ~ over the n in Lorna
Please submit some vertical designs
Please include the world
Please make eagle a watermark
Make sure the Open Horizon doesnt have "preparatory school" under it
I am open to new designs and I will pay more after I chose a designer who seems to get all this stuff in my head!
Reason: Last minute designs were wonderful
Reason: I was out of town and not able to review the wonderful designs posted. I am narrowing the designs down now! I appreciate all the work done thus far.
Hello,
Thank you for all the designs. This is difficult. I have not been able to access them as I was able to last week so please be patient. If you also do web design please send me a message.
Again, thank you. I am down to just a few designs.
Sincerely,
Lorna Vickers Dunmore
I have been extremely busy, I should pick a design by the ned of this week. Thank you for your patience
Industry/Entity Type
Business
Contact Information for Business Card
Dr. Lorna Vickers Dunmore
www.ohacad.example
(555) 284-9306 US
lornajeanvickers@mailbox.example

```html
<!DOCTYPE html>
<html lang="en">
<head>
<meta charset="utf-8">
<title>Open Horizon – Business Card</title>
<link rel="stylesheet" href="https://fonts.googleapis.com/css2?family=Arimo:wght@400;700&family=Roboto+Condensed:wght@700&display=swap">
<style>
  :root {
    --backdrop: #dcdcdd;
    --paper: #fbfbfa;
    --berry-light: #b0006a;
    --berry-mid: #8c0650;
    --berry-deep: #5e0a33;
    --gold: #c9ab16;
    --white: #ffffff;
  }
  * { margin: 0; padding: 0; box-sizing: border-box; }
  html, body {
    width: 1200px;
    height: 1011px;
    overflow: hidden;
    background: var(--backdrop);
  }
  .canvas {
    position: relative;
    width: 1200px;
    height: 1011px;
  }
  .business-card {
    position: absolute;
    left: 370px;
    top: 103px;
    width: 460px;
    height: 805px;
    overflow: hidden;
    background:
      radial-gradient(ellipse 90% 55% at 45% 25%, var(--berry-light) 0%, var(--berry-mid) 55%, var(--berry-deep) 100%);
    box-shadow: 0 14px 30px rgba(0,0,0,0.18);
  }
  .header-shape {
    position: absolute;
    left: 0;
    top: 0;
    width: 460px;
    height: 260px;
  }
  .brand {
    position: absolute;
    left: 0;
    right: 0;
    top: 92px;
    display: flex;
    justify-content: center;
    align-items: center;
    gap: 12px;
  }
  .brand-dot {
    width: 34px;
    height: 34px;
    border-radius: 50%;
    background: var(--berry-mid);
  }
  .brand-name {
    font-family: "Roboto Condensed", "Arial Narrow", sans-serif;
    font-weight: 700;
    font-size: 38px;
    letter-spacing: 1px;
    color: var(--gold);
    text-transform: uppercase;
  }
  .contact-block {
    position: absolute;
    left: 56px;
    top: 482px;
  }
  .holder-name {
    font-family: "Roboto Condensed", "Arial Narrow", sans-serif;
    font-weight: 700;
    font-size: 24px;
    color: var(--gold);
    margin-bottom: 16px;
  }
  .contact-list { list-style: none; }
  .contact-item {
    display: flex;
    align-items: center;
    gap: 12px;
    height: 38px;
    font-family: "Arimo", Arial, sans-serif;
    font-size: 19px;
    color: var(--white);
  }
  .contact-icon {
    width: 16px;
    height: 16px;
    flex: none;
  }
</style>
</head>
<body>
<main class="canvas">
  <article class="business-card">
    <svg class="header-shape" viewBox="0 0 460 260" aria-hidden="true">
      <path d="M0 0 H460 V145 Q230 345 0 145 Z" fill="var(--paper)"/>
      <path d="M460 145 Q230 345 0 145" fill="none" stroke="var(--gold)" stroke-width="3"/>
    </svg>

    <div class="brand">
      <span class="brand-dot"></span>
      <span class="brand-name">Open Horizon</span>
    </div>

    <section class="contact-block">
      <h1 class="holder-name">Dr. Lorna Vickers Dunmore</h1>
      <ul class="contact-list">
        <li class="contact-item">
          <svg class="contact-icon" viewBox="0 0 16 16" aria-hidden="true">
            <circle cx="8" cy="8" r="8" fill="var(--white)"/>
            <path d="M5.2 4.2 L6.6 4 L7.4 6 L6.5 6.8 Q7.3 8.6 9.1 9.5 L9.9 8.6 L11.9 9.4 L11.7 10.8 Q8.5 11.8 6 9.2 Q4.3 7.2 5.2 4.2 Z" fill="var(--berry-deep)"/>
          </svg>
          <span>(555) 284-9306 US</span>
        </li>
        <li class="contact-item">
          <svg class="contact-icon" viewBox="0 0 16 16" aria-hidden="true">
            <circle cx="8" cy="8" r="8" fill="var(--white)"/>
            <rect x="4" y="5" width="8" height="6" fill="none" stroke="var(--berry-deep)" stroke-width="1.1"/>
            <path d="M4 5 L8 8.5 L12 5" fill="none" stroke="var(--berry-deep)" stroke-width="1.1"/>
          </svg>
          <span>lornajeanvickers@mailbox.example</span>
        </li>
        <li class="contact-item">
          <svg class="contact-icon" viewBox="0 0 16 16" aria-hidden="true">
            <circle cx="8" cy="8" r="8" fill="var(--white)"/>
            <circle cx="8" cy="8" r="4.2" fill="none" stroke="var(--berry-deep)" stroke-width="1"/>
            <ellipse cx="8" cy="8" rx="1.8" ry="4.2" fill="none" stroke="var(--berry-deep)" stroke-width="0.9"/>
            <line x1="3.8" y1="8" x2="12.2" y2="8" stroke="var(--berry-deep)" stroke-width="0.9"/>
          </svg>
          <span>www.ohacad.example</span>
        </li>
      </ul>
    </section>
  </article>
</main>
</body>
</html>
```